Tall Fern Roofing Business Card

Need a business card with the logo that was designed here

Contact Information for Business Card

Name, Title, Phone, Email, Website, Company name

```html
<!DOCTYPE html>
<html lang="en">
<head>
<meta charset="utf-8">
<title>Tall Fern Roofing – Business Card</title>
<link href="https://fonts.googleapis.com/css2?family=Poppins:wght@400;600;700&display=swap" rel="stylesheet">
<style>
  :root{
    --bg:#c4c4c4;
    --card-white:#ffffff;
    --brand-blue:#1b76be;
    --brand-blue-light:#2a93e8;
    --text-grey:#4a4a4a;
    --divider:#bdbdbd;
  }
  *{margin:0;padding:0;box-sizing:border-box}
  html,body{width:1093px;height:1200px;overflow:hidden}
  body{background:var(--bg);font-family:"Poppins",sans-serif;position:relative}

  .card{position:absolute;left:265px;width:578px;height:356px;border-radius:26px}
  .card--front{top:226px;background:var(--card-white)}
  .card--back{top:621px;width:581px;background:var(--brand-blue);display:flex;align-items:center;justify-content:center}

  .wordmark{position:absolute;left:30px;top:160px;width:236px;display:flex;align-items:center;gap:8px;
    color:var(--brand-blue);font-weight:600;font-size:22px;line-height:1.1;white-space:nowrap}
  .wordmark__mark{width:14px;height:14px;background:var(--brand-blue);flex:none}

  .divider{position:absolute;left:289px;top:74px;width:1px;height:209px;background:var(--divider)}

  .contact{position:absolute;left:311px;top:110px}
  .contact__name{color:var(--brand-blue);font-weight:700;font-size:20px;line-height:1.1;letter-spacing:.2px}
  .contact__title{color:var(--text-grey);font-size:17px;line-height:1.1;margin-top:1px}
  .contact__list{list-style:none;margin-top:30px}
  .contact__item{display:flex;align-items:center;gap:7px;color:var(--text-grey);font-size:17px;line-height:21px}
  .contact__icon{width:15px;height:15px;flex:none;fill:var(--brand-blue)}
  .contact__highlight{color:var(--brand-blue)}

  .wordmark--back{position:static;width:auto;font-size:40px;gap:14px;color:var(--brand-blue-light)}
  .wordmark--back .wordmark__mark{width:26px;height:26px;background:var(--brand-blue-light)}
</style>
</head>
<body>
  <section class="card card--front" aria-label="Business card front">
    <div class="wordmark"><span class="wordmark__mark"></span>Tall Fern Roofing</div>
    <div class="divider"></div>
    <div class="contact">
      <h1 class="contact__name">DANIEL HARPER</h1>
      <p class="contact__title">Managing Director</p>
      <ul class="contact__list">
        <li class="contact__item">
          <svg class="contact__icon" viewBox="0 0 24 24"><path d="M6.6 10.8a15.1 15.1 0 0 0 6.6 6.6l2.2-2.2c.3-.3.7-.4 1-.2 1.1.4 2.3.6 3.6.6.6 0 1 .4 1 1V20c0 .6-.4 1-1 1C10.6 21 3 13.4 3 4c0-.6.4-1 1-1h3.5c.6 0 1 .4 1 1 0 1.3.2 2.5.6 3.6.1.3 0 .7-.2 1z"/></svg>
          044-987 654 321
        </li>
        <li class="contact__item">
          <svg class="contact__icon" viewBox="0 0 24 24"><path d="M2 5h20v14H2z M2 5l10 8 10-8" stroke="#fff" stroke-width="1.5"/></svg>
          hello@tallfern.com
        </li>
        <li class="contact__item">
          <svg class="contact__icon" viewBox="0 0 24 24"><circle cx="12" cy="12" r="10"/><path d="M2 12h20M12 2c3 3 3 17 0 20M12 2c-3 3-3 17 0 20M4 7h16M4 17h16" stroke="#fff" stroke-width="1.2" fill="none"/></svg>
          <span>www.<span class="contact__highlight">tallfernroofs</span>.com</span>
        </li>
      </ul>
    </div>
  </section>

  <section class="card card--back" aria-label="Business card back">
    <div class="wordmark wordmark--back"><span class="wordmark__mark"></span>Tall Fern Roofing</div>
  </section>
</body>
</html>
```